Car rental website design for a UAE car rental company

This project is about creating a new website design for a car rental company located in Dubai (United Arab Emirates), I opened the same project a few months ago but I didn't receive a lot of appealing entries so I closed it but this time I am marking the project as guaranteed to avoid such situation again, if you have already provided a design before then please re-submit again on this project so that it is considered while reviewing all the designs

A few important things:

1- We need a simple non-complex design
2- The final deliverable would be 2 screens (PSD, JPEG ... etc), the first screen is for the home page and the second screen is for an internal page
3- The home page must have a section that end users can use to rent a car online directly from the home page instead of going into some inner pages
4- The current website is very old and not very appealing so avoid creating a similar design (www.crestvane-autos.example)
5- The name is Crestvane but the company rents normal cars (no Limousin cars will be rented) so avoid adding any fancy cars in the images/graphics used in the design, just normal end users cars
6- The expected pages would be: home, About us, Our team, Strategy, Contact us and links to social media pages
7- The attachments include the company's logo and some screens from other car rental companies that provide online rentals/payments

If you have any questions please feel free to ask and please note that we will need the designs urgently

Thanks

Target Market(s)

Dubai - United Arab Emirates

Industry/Entity Type

It Company

Number of Pages Required

2 page

Font styles to use
Sans Serif

Requirements
Must have
• Check the project details
Nice to have
Should not have

```html
<!DOCTYPE html>
<html lang="en">
<head>
<meta charset="utf-8">
<title>Crestvane – Car Rental Dubai</title>
<link href="https://fonts.googleapis.com/css2?family=Open+Sans:ital,wght@0,400;0,600;0,700;1,400&family=Oswald:wght@500&family=Lobster&display=swap" rel="stylesheet">
<style>
:root{
  --maroon:#8c0f2b;
  --maroon-dark:#6f0a21;
  --ink:#333;
  --muted:#666;
  --light:#ececec;
  --paper:#fff;
  --charcoal:#2e2e2e;
  --charcoal-deep:#1d1d1d;
  --field:#fff;
}
*{margin:0;padding:0;box-sizing:border-box}
html,body{width:1200px;height:2260px;overflow:hidden}
body{font-family:"Open Sans",Arial,sans-serif;color:var(--ink);background:var(--paper);font-size:14px;line-height:1.6}

/* header */
.site-header{height:112px;background:var(--paper);position:relative}
.brand{position:absolute;left:150px;top:18px;display:flex;align-items:center;gap:12px}
.brand-mark{width:44px;height:44px;background:var(--maroon)}
.brand-name{font-weight:700;font-size:26px;color:var(--charcoal)}
.call{position:absolute;right:150px;top:26px;text-align:right}
.call-label{font-size:13px;font-weight:700;color:var(--charcoal);letter-spacing:.5px}
.call-number{font-size:30px;font-weight:700;color:var(--charcoal);line-height:1.1}

/* nav */
.main-nav{position:absolute;left:140px;top:112px;width:920px;height:56px;background:var(--maroon);display:flex;z-index:2;box-shadow:0 3px 6px rgba(0,0,0,.35)}
.main-nav a{color:#fff;text-decoration:none;font-size:17px;padding:0 21px;line-height:56px;border-right:1px solid rgba(255,255,255,.25);white-space:nowrap}
.main-nav a:last-child{border-right:0}
.main-nav a.active{background:var(--maroon-dark)}

/* hero */
.hero{position:relative;height:384px;background:var(--charcoal-deep)}
.hero-photo{position:absolute;inset:0;background:linear-gradient(180deg,#5a5a5a 0%,#3a3a3a 45%,#222 100%)}
.hero-arrow{position:absolute;top:214px;width:38px;height:38px;border-radius:50%;background:#fff;display:flex;align-items:center;justify-content:center}
.hero-arrow.prev{left:30px}.hero-arrow.next{right:30px}
.hero-caption{position:absolute;left:170px;top:320px;font-family:"Lobster",cursive;color:#fff;font-size:32px;line-height:1.3}
.btn{display:inline-block;background:var(--maroon);color:#fff;font-size:15px;text-transform:uppercase;padding:0 26px;line-height:48px;text-decoration:none;letter-spacing:.5px;white-space:nowrap}
.hero .btn{position:absolute;right:150px;top:300px}

/* about */
.about{background:var(--light);height:284px;text-align:center;padding-top:26px}
.section-title{font-family:"Oswald",sans-serif;font-weight:500;color:var(--maroon);font-size:26px;text-transform:uppercase;letter-spacing:1px;line-height:1.3}
.about .rule{width:860px;height:1px;background:#cfcfcf;margin:8px auto 16px}
.about p{width:860px;margin:0 auto 20px;text-align:left;font-size:14px;color:var(--muted)}

/* premier */
.premier{height:360px;display:flex;gap:40px;padding:22px 0 0 170px}
.video{width:390px;height:292px;position:relative}
.video-frame{position:absolute;inset:0 0 30px 0;background:linear-gradient(160deg,#c9c9c9,#8a8a8a)}
.video-bar{position:absolute;left:0;right:0;bottom:0;height:30px;background:#111;display:flex;align-items:center;gap:12px;padding:0 10px}
.video-track{flex:1;height:4px;background:#555}
.premier-body{width:430px;padding-top:8px}
.premier-body .section-title{font-size:24px}
.premier-body p{font-size:13.5px;color:var(--muted);margin:8px 0 16px}

/* reservation */
.reservation{height:310px;background:var(--charcoal);position:relative}
.res-tab{position:absolute;left:50%;transform:translateX(-50%);top:0;background:var(--maroon);color:#fff;font-size:16px;line-height:46px;padding:0 36px;text-transform:uppercase;white-space:nowrap}
.res-grid{position:absolute;left:170px;top:96px;width:860px}
.res-row{display:flex;gap:40px;margin-bottom:22px}
.field label{display:block;color:#fff;font-size:15px;margin-bottom:8px}
.input{height:42px;background:var(--field);display:flex;align-items:center;justify-content:flex-end;padding:0 8px}
.date-group{display:flex;gap:10px}
.select{height:42px;background:var(--field);width:80px;display:flex;align-items:center;justify-content:flex-end;padding-right:8px}
.reservation .btn{margin-top:30px;line-height:44px}

/* rates */
.rates{height:370px;display:flex;padding:44px 0 0 170px;gap:40px}
.rates-body{width:470px}
.rates-body p{font-size:13.5px;color:var(--muted);margin:10px 0 18px}
.rates-photo{width:350px;height:190px;background:linear-gradient(180deg,#e4e4e4,#6b6b6b 70%,#2a2a2a)}

/* testimonial */
.testimonial{height:280px;background:var(--light);text-align:center;padding-top:22px}
.quote-icon{width:62px;height:62px;border-radius:50%;background:var(--paper);margin:0 auto 14px;display:flex;align-items:center;justify-content:center}
.testimonial blockquote{font-size:23px;font-style:italic;color:var(--ink);width:780px;margin:0 auto;line-height:1.45}
.testimonial cite{display:block;font-style:normal;color:var(--maroon);font-size:14px;margin-top:10px;letter-spacing:.5px}
.dots{display:flex;gap:8px;justify-content:center;margin-top:10px}
.dots span{width:8px;height:8px;border-radius:50%;background:#bbb}
.dots span.on{background:var(--maroon)}

/* footer */
.site-footer{height:160px;background:var(--charcoal-deep);position:relative;color:#ddd;font-size:13px}
.footer-links{position:absolute;left:170px;top:52px}
.footer-copy{position:absolute;left:170px;top:78px;color:#aaa}
.social{position:absolute;right:170px;top:50px;display:flex;gap:10px}
.social a{width:34px;height:34px;border-radius:50%;background:#fff}
</style>
</head>
<body>

<header class="site-header">
  <div class="brand"><span class="brand-mark"></span><span class="brand-name">Crestvane</span></div>
  <div class="call">
    <div class="call-label">CALL FOR CAR RENTAL</div>
    <div class="call-number">04-555-0142</div>
  </div>
  <nav class="main-nav">
    <a class="active" href="#">Home</a><a href="#">About us</a><a href="#">Our team</a><a href="#">Vehicles</a><a href="#">Strategy</a><a href="#">My Bookings</a><a href="#">Contact us</a>
  </nav>
</header>

<section class="hero">
  <div class="hero-photo" role="img" aria-label="Everyday family sedan parked in a dim garage"></div>
  <span class="hero-arrow prev"><svg width="14" height="14" viewBox="0 0 14 14"><path d="M9 2 4 7l5 5" stroke="#333" stroke-width="2.2" fill="none"/></svg></span>
  <span class="hero-arrow next"><svg width="14" height="14" viewBox="0 0 14 14"><path d="M5 2l5 5-5 5" stroke="#333" stroke-width="2.2" fill="none"/></svg></span>
  <div class="hero-caption">Lorem Ipsum is simply dummy tex</div>
  <a class="btn" href="#">Book a reservation</a>
</section>

<section class="about">
  <h2 class="section-title">About us</h2>
  <div class="rule"></div>
  <p>Crestvane Car Rental was founded in Dubai to make renting an everyday car simple, quick and fairly priced. Our fleet of clean, well kept sedans, hatchbacks and family SUVs is ready for daily errands, business trips or weekend drives across the Emirates. Choose your car online, pick it up at a branch or have it delivered to your door, and return it whenever your plans are done. Friendly support is available around the clock in English and Arabic.</p>
  <a class="btn" href="#">Read more</a>
</section>

<section class="premier">
  <div class="video">
    <div class="video-frame" role="img" aria-label="Video still of a customer collecting a rental car"></div>
    <div class="video-bar">
      <svg width="12" height="12" viewBox="0 0 12 12"><path d="M2 1l9 5-9 5z" fill="#fff"/></svg>
      <span class="video-track"></span>
      <svg width="14" height="12" viewBox="0 0 14 12"><path d="M1 4h3l4-3v10L4 8H1z" fill="#fff"/></svg>
    </div>
  </div>
  <div class="premier-body">
    <h2 class="section-title">A simple car rental service</h2>
    <p>Renting with Crestvane takes only a few minutes. Pick your dates, choose from compact, sedan or family models, and confirm your booking online with secure payment. Every car is serviced, insured and fully cleaned before each rental, with clear prices and no hidden fees. Collect your car at our Dubai branches or the airport, or ask for free delivery within the city. Daily, weekly and monthly plans fit every trip, from a short visit to a long stay in the UAE.</p>
    <a class="btn" href="#">Read more</a>
  </div>
</section>

<section class="reservation">
  <div class="res-tab">Reservation form</div>
  <div class="res-grid">
    <div class="res-row">
      <div class="field" style="width:230px"><label>Pick-up Date</label><div class="input"><svg width="18" height="18" viewBox="0 0 18 18"><rect x="2" y="4" width="14" height="12" fill="none" stroke="#555" stroke-width="1.6"/><path d="M2 8h14M6 2v4M12 2v4" stroke="#555" stroke-width="1.6"/></svg></div></div>
      <div class="field" style="width:310px"><label>Drop-off Date</label>
        <div class="date-group">
          <div class="input" style="width:110px"><svg width="18" height="18" viewBox="0 0 18 18"><rect x="2" y="4" width="14" height="12" fill="none" stroke="#555" stroke-width="1.6"/><path d="M2 8h14M6 2v4M12 2v4" stroke="#555" stroke-width="1.6"/></svg></div>
          <div class="select"><svg width="10" height="6" viewBox="0 0 10 6"><path d="M0 0h10L5 6z" fill="#555"/></svg></div>
          <div class="select"><svg width="10" height="6" viewBox="0 0 10 6"><path d="M0 0h10L5 6z" fill="#555"/></svg></div>
        </div>
      </div>
      <div class="field" style="width:240px"><label>Number of Passengers</label><div class="input"></div></div>
    </div>
    <div class="res-row">
      <div class="field" style="width:230px"><label>Pick-up Location</label><div class="input"></div></div>
      <div class="field" style="width:310px"><label>Drop-off Location</label><div class="input"></div></div>
      <div class="field"><a class="btn" href="#">Reservation</a></div>
    </div>
  </div>
</section>

<section class="rates">
  <div class="rates-body">
    <h2 class="section-title">Everyday cars at fair rates</h2>
    <p>Crestvane offers reliable cars for every budget with short notice. Our economy hatchbacks, family sedans and seven seat SUVs are very affordable and always available for last minute booking. Our clear daily rates include insurance and road assistance, so you can drive around Dubai and the Emirates without worrying about quality of service or surprise charges. ... More Info</p>
    <a class="btn" href="#">Read more</a>
  </div>
  <div class="rates-photo" role="img" aria-label="Compact family car parked outdoors"></div>
</section>

<section class="testimonial">
  <div class="quote-icon"><svg width="30" height="24" viewBox="0 0 30 24"><path d="M2 22V12C2 6 5 2 11 1v4C7 6 6 9 6 12h6v10zM18 22V12c0-6 3-10 9-11v4c-4 1-5 4-5 7h6v10z" fill="#333"/></svg></div>
  <blockquote>"Fusce dapibus, tellus ac cursus commodo, tortor mauris condimentum. Duis mollis, est non commodo luctus, nisi erat"</blockquote>
  <cite>LEENA MARWAN, BRIGHTPOST</cite>
  <div class="dots"><span class="on"></span><span></span><span></span><span></span></div>
</section>

<footer class="site-footer">
  <div class="footer-links">Terms &amp; Conditions &nbsp;|&nbsp; Privacy Policy &nbsp;|&nbsp; Contact &nbsp;|&nbsp; Client Support</div>
  <div class="footer-copy">Copyright © 2014. All rights Reserved</div>
  <div class="social" aria-label="Social media pages"><a href="#" aria-label="Social page 1"></a><a href="#" aria-label="Social page 2"></a><a href="#" aria-label="Social page 3"></a><a href="#" aria-label="Social page 4"></a></div>
</footer>

</body>
</html>
```